A letter fromthe tooth fairy

We our looking for a design of a fairy (tooth fairy) its for a letter we our doing. The letter is a note from the tooth fairy. We already have the wording done we just need the fairy and the board of the letter done! We want the fairy to be a woman with some age to her and we want her to look magical but not futuristic , also we want her charming but not sexy this is for small children. We also would like the boarder of the letter to look magical. Last the fairy needs to be at angle like flying. The angle needs to be a little to the right (I guess what I mean is if you were looking at a clock her head would be at 1or 2 on a clock and her feet at 7or 8 on a clock.

```html
<!DOCTYPE html>
<html lang="en">
<head>
<meta charset="utf-8">
<title>A Letter from the Tooth Fairy</title>
<link rel="stylesheet" href="https://fonts.googleapis.com/css2?family=Courgette&display=swap">
<style>
  :root {
    --paper: #ffffff;
    --ink: #111111;
    --fairy-hair: #f3ef8a;
    --fairy-dress: #2f5fd6;
    --fairy-wing: #bfeef0;
    --swirl-blue: #8ec3ef;
    --confetti-pink: #f2a6e6;
    --confetti-yellow: #f6ec7a;
  }
  * { margin: 0; padding: 0; box-sizing: border-box; }
  html, body {
    width: 848px;
    height: 1200px;
    overflow: hidden;
    background: var(--paper);
  }
  .letter {
    position: relative;
    width: 848px;
    height: 1200px;
    background: var(--paper);
    overflow: hidden;
  }
  .fairy-illustration {
    position: absolute;
    left: 25px;
    top: 0;
    width: 240px;
    height: 338px;
    border-radius: 46% 46% 40% 40%;
    background: linear-gradient(160deg, var(--fairy-hair) 0%, var(--fairy-wing) 38%, var(--fairy-dress) 78%, #ffffff 100%);
    opacity: 0.85;
  }
  .corner-flourish {
    position: absolute;
    width: 312px;
    height: 314px;
  }
  .corner-flourish--top-right {
    right: 0;
    top: 0;
    background: radial-gradient(circle at 100% 0%, var(--swirl-blue) 0%, var(--confetti-pink) 40%, var(--confetti-yellow) 58%, rgba(255,255,255,0) 72%);
  }
  .corner-flourish--bottom-left {
    left: 0;
    bottom: 0;
    background: radial-gradient(circle at 0% 100%, var(--swirl-blue) 0%, var(--confetti-pink) 40%, var(--confetti-yellow) 58%, rgba(255,255,255,0) 72%);
  }
  .corner-flourish--bottom-right {
    right: 0;
    bottom: 0;
    background: radial-gradient(circle at 100% 100%, var(--swirl-blue) 0%, var(--confetti-pink) 40%, var(--confetti-yellow) 58%, rgba(255,255,255,0) 72%);
  }
  .letter-body {
    position: absolute;
    left: 102px;
    top: 432px;
    width: 680px;
    font-family: "Courgette", cursive;
    font-size: 33px;
    line-height: 40.5px;
    color: var(--ink);
  }
  .letter-signature {
    margin-top: 40.5px;
  }
</style>
</head>
<body>
  <main class="letter">
    <div class="fairy-illustration" role="img" aria-label="Illustration of a flying tooth fairy with yellow hair, wings and a blue dotted dress, holding a large tooth"></div>
    <div class="corner-flourish corner-flourish--top-right" role="img" aria-label="Magical corner ornament of blue swirls with colourful stars and sparkles"></div>
    <div class="corner-flourish corner-flourish--bottom-left" role="img" aria-label="Magical corner ornament of blue swirls with colourful stars and sparkles"></div>
    <div class="corner-flourish corner-flourish--bottom-right" role="img" aria-label="Magical corner ornament of blue swirls with colourful stars and sparkles"></div>

    <section class="letter-body">
      <p class="letter-message">
        Congratulations! I heard you lost<br>
        your first tooth. So I had to come<br>
        check for myself. Looks great, so I left<br>
        you a surprise under your pillow.<br>
        Keep up the good work on brushing<br>
        your teeth at least twice a day! I will<br>
        be visiting you again on<br>
        another day!
      </p>
      <p class="letter-signature">The Tooth Fairy</p>
    </section>
  </main>
</body>
</html>
```